Wedding filmmaker needs artistic business card design - brightwaterreels.ca

We are high end wedding filmmakers in a major market who produce cinematic wedding films. We require a business card design that communicates our quality, artistry, and professionalism yet looks progressive and friendly. Colors and design should skew appeal more to the bride-to-be who is usually the decision maker but not be overtly feminine per se. This means generally light pastel shades of ivory, purple, pink, yellow, as examples.
We already have a name logo established: the words "Brightwater Reels" in the font Great Vibes. Designs must use Kraft natural cardstock as the print stock and am leaning heavily toward our name logo in white, but I am open to black as well. Please design any color elements with spot white underneath where possible.
Do not try to compliment or take inspiration from our website design. Treat the card design as a separate stand alone.
Thank you so much for your hard work!

Target Market(s)

Affluent couples spending $50,000+ on their wedding

Industry/Entity Type

Progressive

Contact Information for Business Card

Peter Brightwater
Producer
905-482-7139
www.brightwaterreels.ca
peter@brightwaterreels.ca
twitter @brightwater287

Font styles to use
Serif
Sans Serif

Requirements
Must have
• - Brightwater Reels name logo (reference GIF uploaded for reference only) and catch phrase: Breathtaking wedding films (I'm open to capitalizing all three words, or just first, or all in small caps). I favor logo, and catch phrase on front of card and my contact details on the other side but if you feel strongly about a different design, go for it!
• - Design must be submitted shown on Kraft natural cardstock NOT WHITE cardstock, If you're not familiar with Kraft, this is what it looks like: http://www.quillandlatchjournal.com/wp-content/uploads/2013/07/il_570xN.382745196_kq3m.jpg
Nice to have
• - An original graphic element (eg. movie reel, bouquet, confetti, etc.) that compliments the name logo but is subtle and discreet, doesn't overpower or entangle it.
• -Great use of balance, composition, negative space, etc. I like clean tasteful design
Should not have
• -Lousy boring clip art.
• -Graphic elements, fonts, or color palette from our website
• -White cardstock background
• -designs you have previously submitted for other contests
• -Bold dark colors (eg. red, orange navy blue, etc.)
• -High tech futuristic designs like you'd create for a software company

```html
<!DOCTYPE html>
<html lang="en">
<head>
<meta charset="UTF-8">
<title>Brightwater Reels – Business Card</title>
<link rel="stylesheet" href="https://fonts.googleapis.com/css2?family=Great+Vibes&family=Exo+2:wght@400;600&family=Cormorant+Garamond:ital,wght@0,500;1,500&display=swap">
<style>
  :root {
    --bg: #ece8e2;
    --kraft: #c9a77c;
    --kraft-light: #d6b78f;
    --kraft-dark: #b8946a;
    --lavender: #b7a3c8;
    --lavender-line: #d6c9e1;
    --ink: #4a3a2c;
    --white: #ffffff;
  }
  * { margin: 0; padding: 0; box-sizing: border-box; }
  html, body {
    width: 1200px;
    height: 905px;
    overflow: hidden;
    background: var(--bg);
  }
  .canvas {
    position: relative;
    width: 1200px;
    height: 905px;
  }
  .card {
    position: absolute;
    width: 560px;
    height: 320px;
    overflow: hidden;
    box-shadow: 0 6px 18px rgba(0, 0, 0, 0.16);
    background: linear-gradient(100deg, var(--kraft-dark) 0%, var(--kraft-light) 50%, var(--kraft) 100%);
  }

  /* Front */
  .card-front {
    left: 60px;
    top: 110px;
  }
  .front-band {
    position: absolute;
    left: 0;
    right: 0;
    top: 96px;
    height: 128px;
    background: var(--lavender);
    display: flex;
    flex-direction: column;
    align-items: center;
    justify-content: center;
  }
  .wordmark {
    font-family: "Great Vibes", cursive;
    font-weight: 400;
    white-space: nowrap;
    line-height: 1;
  }
  .front-band .wordmark {
    font-size: 50px;
    color: var(--white);
  }
  .tagline {
    margin-top: 8px;
    font-family: "Cormorant Garamond", serif;
    font-style: italic;
    font-weight: 500;
    font-size: 15px;
    letter-spacing: 2px;
    color: var(--white);
  }

  /* Back */
  .card-back {
    left: 580px;
    top: 470px;
  }
  .back-brand {
    position: absolute;
    left: 0;
    width: 300px;
    top: 112px;
    text-align: center;
  }
  .back-brand .wordmark {
    font-size: 34px;
    color: var(--white);
  }
  .person {
    position: absolute;
    left: 0;
    width: 300px;
    top: 246px;
    text-align: center;
    font-family: "Exo 2", sans-serif;
    color: var(--ink);
  }
  .person-name {
    font-size: 19px;
    font-weight: 600;
    letter-spacing: 1px;
  }
  .person-role {
    font-size: 8.5px;
    letter-spacing: 1.5px;
    margin-top: 2px;
  }
  .contact-panel {
    position: absolute;
    left: 0;
    top: 0;
    width: 560px;
    height: 320px;
  }
  .contact-list {
    position: absolute;
    left: 372px;
    top: 0;
    width: 188px;
    list-style: none;
    font-family: "Exo 2", sans-serif;
    color: var(--white);
    font-size: 11.5px;
    letter-spacing: 0.3px;
  }
  .contact-list li {
    height: 80px;
    display: flex;
    align-items: center;
    padding-left: 10px;
    white-space: nowrap;
  }
  .at-mark {
    position: absolute;
    left: 334px;
    top: 264px;
    width: 24px;
    text-align: center;
    font-family: "Exo 2", sans-serif;
    font-weight: 600;
    font-size: 22px;
    line-height: 32px;
    color: var(--white);
  }
</style>
</head>
<body>
<main class="canvas">

  <section class="card card-front" aria-label="Card front">
    <div class="front-band">
      <span class="wordmark">Brightwater Reels</span>
      <span class="tagline">Breathtaking Wedding Films</span>
    </div>
  </section>

  <section class="card card-back" aria-label="Card back">
    <div class="back-brand"><span class="wordmark">Brightwater Reels</span></div>
    <div class="person">
      <div class="person-name">PETER BRIGHTWATER</div>
      <div class="person-role">PRODUCER</div>
    </div>

    <svg class="contact-panel" viewBox="0 0 560 320" aria-hidden="true">
      <polygon fill="var(--lavender)" points="320,0 560,0 560,320 320,320 320,80 310,80 290,96 296,80 290,80 290,18 320,18"/>
      <g stroke="var(--lavender-line)" stroke-width="1.2">
        <line x1="320" y1="80" x2="560" y2="80"/>
        <line x1="320" y1="160" x2="560" y2="160"/>
        <line x1="320" y1="240" x2="560" y2="240"/>
        <line x1="372" y1="12" x2="372" y2="68"/>
        <line x1="372" y1="92" x2="372" y2="148"/>
        <line x1="372" y1="172" x2="372" y2="228"/>
        <line x1="372" y1="252" x2="372" y2="308"/>
      </g>
      <path fill="var(--white)" d="M337 40c1-3 3-5 5-5l3 6-2 3c1 3 4 6 7 7l3-2 6 3c0 2-2 4-5 5-8 0-17-9-17-17z"/>
      <g fill="none" stroke="var(--white)" stroke-width="1.8">
        <rect x="334" y="112" width="24" height="16"/>
        <polyline points="334,112 346,122 358,112"/>
      </g>
      <g fill="none" stroke="var(--white)" stroke-width="1.6">
        <circle cx="346" cy="200" r="11"/>
        <ellipse cx="346" cy="200" rx="5" ry="11"/>
        <line x1="335" y1="200" x2="357" y2="200"/>
        <line x1="337" y1="194" x2="355" y2="194"/>
        <line x1="337" y1="206" x2="355" y2="206"/>
      </g>
    </svg>
    <span class="at-mark" aria-hidden="true">@</span>

    <ul class="contact-list">
      <li>905-482-7139</li>
      <li>peter@brightwaterreels.ca</li>
      <li>www.brightwaterreels.ca</li>
      <li>@brightwater287</li>
    </ul>
  </section>

</main>
</body>
</html>
```